Looking for business card/letterhead/email signature

Take existing logo and create full design suite of collateral

Contact Information for Business Card

Use mock details that can be edited by us

Font styles to use
Sans Serif

```html
<!DOCTYPE html>
<html lang="en">
<head>
<meta charset="utf-8">
<title>Harlow Digital – Stationery Suite</title>
<link href="https://fonts.googleapis.com/css2?family=Roboto:wght@300;400;500;700&display=swap" rel="stylesheet">
<style>
:root{
  --navy:#0b4a8b;
  --blue:#2a9bd6;
  --orange:#e8841f;
  --lime:#b8c937;
  --pink:#d92a6b;
  --red:#e02a4a;
  --paper:#ececec;
  --ink:#555a60;
  --bg:#dfe0e2;
}
*{margin:0;padding:0;box-sizing:border-box}
html,body{width:1200px;height:940px;overflow:hidden}
body{background:var(--bg);font-family:'Roboto',sans-serif;color:var(--ink);position:relative}
.piece{position:absolute;background:var(--paper);box-shadow:0 4px 14px rgba(0,0,0,.18);overflow:hidden}
.abs{position:absolute}
.icon{width:7px;height:7px;vertical-align:-1px;margin-right:3px;fill:none;stroke:var(--navy);stroke-width:1.4}

/* wordmark */
.wordmark{position:absolute;display:flex;align-items:center;gap:4px}
.wordmark .name{font-weight:700;color:var(--navy);letter-spacing:-.02em;line-height:1}
.wordmark .dot{border-radius:50%;background:var(--navy)}
.wordmark-sub{position:absolute;font-weight:400;color:var(--navy);letter-spacing:.22em;line-height:1}

/* business card front */
.card-front{left:226px;top:70px;width:286px;height:164px}
.card-front .divider{left:143px;top:46px;width:1px;height:61px;background:#7d8288}
.card-front .divider-accent{left:142px;top:46px;width:2px;height:14px;background:var(--navy)}
.card-front .person{left:171px;top:45px}
.person-name{font-weight:700;color:var(--navy)}
.card-front .person-name{font-size:8px}
.card-front .person-role{font-size:5.2px;color:var(--ink)}
.card-front .addr{left:171px;top:76px;font-size:5.2px;line-height:7.6px}
.card-front .contacts{left:171px;top:96px;font-size:5.6px;line-height:8px}
.card-front .footer{left:0;bottom:0;width:286px;height:18px}

/* business card back */
.card-back{left:226px;top:266px;width:286px;height:164px;background:var(--navy)}
.color-bar{position:absolute;left:0;bottom:0;width:100%;display:flex}
.color-bar span{flex:1}
.color-bar .c1{background:var(--lime)}
.color-bar .c2{background:var(--pink)}
.color-bar .c3{background:var(--blue)}
.color-bar .c4{background:var(--orange)}
.color-bar .c5{background:var(--red)}

/* email signature */
.signature-block{left:74px;top:462px;width:438px;height:134px}
.signature-block .person{left:146px;top:33px}
.signature-block .person-name{font-size:11px}
.signature-block .person-role{font-size:8px;margin-top:1px}
.signature-block .contacts{left:146px;top:62px;font-size:7.6px;line-height:10.3px}
.signature-block .divider{left:250px;top:34px;width:1px;height:70px;background:#9a9ea3}
.follow{left:263px;top:45px;font-size:7.6px;display:flex;align-items:center;gap:3px}
.follow i{display:inline-block;width:8px;height:8px;border-radius:50%;background:var(--navy)}
.signature-block .addr{left:263px;top:72px;font-size:7.4px;line-height:10.2px}

/* letterhead */
.letterhead{left:561px;top:71px;width:565px;height:798px}
.lh-address{right:174px;top:46px;text-align:right;font-size:8.6px;line-height:11.4px;font-weight:300;color:var(--ink)}
.lh-divider{left:406px;top:34px;width:1px;height:45px;background:#7d8288}
.lh-contacts{left:421px;top:34px;font-size:8.6px;line-height:11.6px;font-weight:300}
.letter{left:62px;width:440px;font-size:8.6px;line-height:11.4px;font-weight:300;color:var(--ink)}
.letter-date{top:185px}
.letter-greeting{top:220px}
.letter-body{top:243px;text-align:justify}
.letter-body p{margin-bottom:11.4px}
.letter-closing{top:527px}
.signature-mark{left:62px;top:546px;width:110px;height:24px;background:linear-gradient(90deg,rgba(60,60,60,.18),rgba(60,60,60,.05));border-radius:3px}
.letter-signoff{top:572px}
.letterhead .footer{left:0;bottom:0;width:565px;height:24px}
.footer-url{position:absolute;color:#fff;font-weight:300;white-space:nowrap}
.footer-url b{font-weight:700}
</style>
</head>
<body>

<svg width="0" height="0" style="position:absolute">
  <defs>
    <symbol id="i-phone" viewBox="0 0 10 10"><path d="M2 1l2 2-1 1.5c.7 1.3 1.5 2.1 2.5 2.5L7 6l2 2-1.5 1.5C5 9 1 5 .5 2.5z"/></symbol>
    <symbol id="i-mobile" viewBox="0 0 10 10"><rect x="2.5" y=".8" width="5" height="8.4" rx="1"/></symbol>
    <symbol id="i-mail" viewBox="0 0 10 10"><rect x=".8" y="2" width="8.4" height="6"/><path d="M.8 2L5 5.5 9.2 2"/></symbol>
    <symbol id="i-web" viewBox="0 0 10 10"><circle cx="5" cy="5" r="4"/><path d="M1 5h8M5 1c-2 2.5-2 5.5 0 8M5 1c2 2.5 2 5.5 0 8"/></symbol>
  </defs>
</svg>

<!-- Business card – front -->
<section class="piece card-front" aria-label="Business card front">
  <div class="wordmark" style="left:34px;top:72px">
    <span class="name" style="font-size:24px">harlow</span>
    <span class="dot" style="width:7px;height:7px"></span>
  </div>
  <span class="wordmark-sub" style="left:58px;top:96px;font-size:6px">DIGITAL</span>
  <div class="abs divider"></div>
  <div class="abs divider-accent"></div>
  <div class="abs person">
    <div class="person-name">Nora T. Vance</div>
    <div class="person-role">Managing Director</div>
  </div>
  <div class="abs addr">Co.Street, Building/Suite<br>City/State, Zip Code</div>
  <div class="abs contacts">
    <div><svg class="icon"><use href="#i-phone"/></svg>410.555.0172</div>
    <div><svg class="icon"><use href="#i-mobile"/></svg>410.555.0198</div>
    <div><svg class="icon"><use href="#i-mail"/></svg>info@harlow-digital.com</div>
  </div>
  <svg class="abs footer" viewBox="0 0 286 18" preserveAspectRatio="none">
    <rect x="0" y="7" width="92" height="4" fill="var(--blue)"/>
    <rect x="200" y="6" width="86" height="4" fill="var(--orange)"/>
    <path d="M0 14H84C96 14 98 2 112 2H174C188 2 190 14 202 14H286V18H0Z" fill="var(--navy)"/>
  </svg>
  <span class="footer-url" style="left:106px;top:152px;font-size:6px">www.<b>harlow-digital</b>.com</span>
</section>

<!-- Business card – back -->
<section class="piece card-back" aria-label="Business card back">
  <div class="wordmark" style="left:74px;top:64px">
    <span class="name" style="font-size:38px;color:#fff">harlow</span>
    <span class="dot" style="width:10px;height:10px;background:#fff"></span>
  </div>
  <span class="wordmark-sub" style="left:108px;top:100px;font-size:10px;color:#fff">DIGITAL</span>
  <div class="color-bar" style="height:5px">
    <span class="c1"></span><span class="c2"></span><span class="c3"></span><span class="c4"></span><span class="c5"></span>
  </div>
</section>

<!-- Email signature -->
<section class="piece signature-block" aria-label="Email signature">
  <div class="wordmark" style="left:22px;top:50px">
    <span class="name" style="font-size:28px">harlow</span>
    <span class="dot" style="width:8px;height:8px"></span>
  </div>
  <span class="wordmark-sub" style="left:50px;top:80px;font-size:7.4px">DIGITAL</span>
  <div class="abs person">
    <div class="person-name">Nora T. Vance</div>
    <div class="person-role">Managing Director</div>
  </div>
  <div class="abs contacts">
    <div><svg class="icon"><use href="#i-phone"/></svg>410.555.0172</div>
    <div><svg class="icon"><use href="#i-mobile"/></svg>410.555.0198</div>
    <div><svg class="icon"><use href="#i-mail"/></svg>info@harlow-digital.com</div>
    <div><svg class="icon"><use href="#i-web"/></svg>www.harlow-digital.com</div>
  </div>
  <div class="abs divider"></div>
  <div class="abs follow">Follow us : <i></i><i></i><i></i></div>
  <div class="abs addr">Harlow Digital<br>Co.Street, Building/Suite<br>City/State, Zip Code</div>
  <div class="color-bar" style="height:6px">
    <span class="c1"></span><span class="c2"></span><span class="c3"></span><span class="c4"></span><span class="c5"></span>
  </div>
</section>

<!-- Letterhead -->
<section class="piece letterhead" aria-label="Letterhead">
  <div class="wordmark" style="left:41px;top:40px">
    <span class="name" style="font-size:34px">harlow</span>
    <span class="dot" style="width:9px;height:9px"></span>
  </div>
  <span class="wordmark-sub" style="left:70px;top:74px;font-size:9px">DIGITAL</span>

  <div class="abs lh-address">Harlow Digital<br>Co.Street, Building/Suite<br>City/State, Zip Code</div>
  <div class="abs lh-divider"></div>
  <div class="abs lh-contacts">
    <div><svg class="icon"><use href="#i-phone"/></svg>410.555.0172</div>
    <div><svg class="icon"><use href="#i-mobile"/></svg>410.555.0198</div>
    <div><svg class="icon"><use href="#i-mail"/></svg>info@harlow-digital.com</div>
    <div><svg class="icon"><use href="#i-web"/></svg>www.harlow-digital.com</div>
  </div>

  <div class="abs letter letter-date">January 01, 2020</div>
  <div class="abs letter letter-greeting">Dear Marcus Lindqvist,</div>
  <div class="abs letter letter-body">
    <p>Lorem ipsum dolor sit amet, consectetuer adipiscing elit, sed diam nonummy nibh euismod tincidunt ut laoreet dolore magna aliquam erat volutpat. Ut wisi enim ad minim veniam, quis nostrud exerci tation ullamcorper suscipit lobortis nisl ut aliquip ex ea commodo consequat. Duis dolore te feugait nulla facilisi. Nam liber tempor cum soluta nobis eleifend option congue nihil imperdiet doming id quod mazim placerat facer possim assum. Duis autem vel eum iriure dolor in hendrerit in vulputate velit esse molestie consequat, vel illum dolore eu feugiat nulla facilisis at vero eros et accumsan et iusto odio dignissim qui blandit praesent luptatum zzril delenit augue duis dolore te feugait nulla facilisi. Consectetuer adipiscing elit, sed diam nonummy nibh euismod tincidunt ut laoreet dolore magna aliquam erat volutpat. Ut wisi enim ad minim veniam, quis nostrud exerci tation ullamcorper suscipit lobortis nisl ut aliquip ex ea commodo consequat.</p>
    <p>Consectetuer adipiscing elit, sed diam nonummy nibh euismod tincidunt ut laoreet dolore magna aliquam erat volutpat. Ut wisi enim ad minim veniam, quis nostrud exerci tation ullamcorper suscipit lobortis nisl ut aliquip ex ea commodo consequat. Consectetuer adipiscing elit, sed diam nonummy nibh euismod tincidunt ut laoreet dolore magna aliquam erat volutpat. Ut wisi enim ad minim veniam, quis nostrud exerci tation ullamcorper suscipit lobortis nisl ut aliquip ex ea commodo consequat.</p>
    <p>Dolor sit amet, consectetuer adipiscing elit, sed diam nonummy nibh euismod tincidunt ut laoreet dolore magna aliquam erat volutpat. Ut wisi enim ad minim veniam, quis nostrud exerci tation ullamcorper suscipit lobortis nisl ut aliquip ex ea commodo consequat. Duis dolore te feugait nulla facilisi. Nam liber tempor cum soluta nobis eleifend option congue nihil imperdiet doming id quod mazim placerat facer possim assum. Duis dolore te feugait nulla facilisi. Nam liber tempor cum soluta nobis eleifend option congue nihil imperdiet doming id quod mazim placerat facer possim assum.Duis dolore te feugait nulla facilisi. Nam liber tempor cum soluta nobis eleifend option congue nihil imperdiet doming id quod mazim placerat facer possim assum.</p>
  </div>
  <div class="abs letter letter-closing">Sincerely Yours,</div>
  <div class="abs signature-mark" role="img" aria-label="Handwritten signature of Simon Ardell"></div>
  <div class="abs letter letter-signoff">Authorized Managing Director<br>Your Company Name</div>

  <svg class="abs footer" viewBox="0 0 565 24" preserveAspectRatio="none">
    <rect x="0" y="9" width="198" height="6" fill="var(--blue)"/>
    <rect x="364" y="8" width="201" height="6" fill="var(--orange)"/>
    <path d="M0 18H190C206 18 210 2 230 2H340C360 2 364 18 380 18H565V24H0Z" fill="var(--navy)"/>
  </svg>
  <span class="footer-url" style="left:230px;top:777px;font-size:9.4px">www.<b>harlow-digital</b>.com</span>
</section>

</body>
</html>
```